Telecommunications/Power civil contractor needs business card design

Were a new telecommunications/power underground civil contractor that is looking for a new business card design. Our company colours are silver or grey and orange. Feel free to use the white background logo or the black background logo.

Target Market(s)

Local contractors, utility companies, private sector mining/energy companies, developers.

Industry/Entity Type

Telecommunications

Contact Information for Business Card

Each card will need the following info:
Persons name:
Title:
E-mail:
Phone number:
Shop Address:
Mailing Address:

Requirements
Must have
• Each card will need the following info:
• Persons name:
• Title:
• E-mail:
• Phone number:
• Shop Address:
• Mailing Address:

```html
<!DOCTYPE html>
<html lang="en">
<head>
<meta charset="utf-8">
<title>Trench Line Contracting Inc – Business Card</title>
<link rel="stylesheet" href="https://fonts.googleapis.com/css2?family=Open+Sans:wght@400;600;700;800&display=swap">
<style>
  :root {
    --orange: #f15a24;
    --grey: #6d6e70;
    --grey-dark: #58595b;
    --ink: #333333;
    --card-white: #ffffff;
    --card-black: #1e1e1e;
    --card-black-edge: #2b2b2b;
    --backdrop: #e9e7e4;
  }
  * { margin: 0; padding: 0; box-sizing: border-box; }
  html, body {
    width: 1200px; height: 900px; overflow: hidden;
    background: var(--backdrop);
    font-family: "Open Sans", Arial, sans-serif;
  }
  .sheet {
    position: relative; width: 1200px; height: 900px;
    display: flex; flex-direction: column; align-items: center; justify-content: center; gap: 44px;
  }
  .card {
    position: relative; width: 620px; height: 354px; overflow: hidden;
    box-shadow: 0 6px 18px rgba(0,0,0,.18);
  }
  .card-back {
    background: linear-gradient(135deg, var(--card-black-edge), var(--card-black) 55%, #141414);
  }
  .card-front { background: var(--card-white); }
  .card-art { position: absolute; inset: 0; width: 100%; height: 100%; }

  .brand {
    position: absolute; display: flex; flex-direction: column; align-items: center; text-align: center;
  }
  .brand-mark {
    width: 96px; height: 96px; border-radius: 50%; margin-bottom: 14px;
  }
  .brand-name {
    font-weight: 800; text-transform: uppercase; line-height: 1.05; letter-spacing: 1px;
  }
  .brand-name .line-main { display: block; font-size: 34px; }
  .brand-name .line-sub { display: block; font-size: 17px; letter-spacing: 2px; }

  .card-back .brand { left: 0; right: 0; top: 64px; }
  .card-back .brand-mark { border: 5px solid #ffffff; }
  .card-back .brand-name { color: #ffffff; }

  .card-front .brand { left: 320px; width: 260px; top: 96px; }
  .card-front .brand-mark { border: 5px solid var(--orange); }
  .card-front .brand-name { color: var(--grey-dark); }

  .contact {
    position: absolute; left: 62px; top: 28px; color: var(--ink);
  }
  .person-name { font-size: 18px; font-weight: 700; color: var(--grey); line-height: 1.1; }
  .person-name .first { color: var(--orange); }
  .person-title { font-size: 12.5px; margin-bottom: 12px; }
  .contact-line { display: flex; align-items: center; gap: 8px; font-size: 13.5px; line-height: 1.45; }
  .contact-line svg { width: 11px; height: 11px; fill: var(--orange); flex: none; }
  .address { margin-top: 10px; font-size: 13.5px; line-height: 1.3; }
  .address + .address { margin-top: 4px; }
  .address-label { color: var(--orange); font-weight: 700; }
</style>
</head>
<body>
<main class="sheet">

  <section class="card card-back" aria-label="Card back">
    <div class="brand">
      <div class="brand-mark"></div>
      <p class="brand-name"><span class="line-main">Trench Line</span><span class="line-sub">Contracting Inc</span></p>
    </div>
  </section>

  <section class="card card-front" aria-label="Card front">
    <svg class="card-art" viewBox="0 0 620 354" aria-hidden="true">
      <polygon points="0,24 34,24 18,52 0,52" fill="var(--orange)"/>
      <polygon points="42,24 56,24 56,52 26,52" fill="var(--grey)"/>
      <polygon points="0,258 294,258 276,282 0,282" fill="var(--orange)"/>
      <polygon points="300,292 620,292 620,330 272,330" fill="var(--grey)"/>
    </svg>

    <div class="contact">
      <p class="person-name"><span class="first">Marcus</span> Hale</p>
      <p class="person-title">Managing Director</p>
      <p class="contact-line">
        <svg viewBox="0 0 24 24"><path d="M6.6 10.8a15.1 15.1 0 0 0 6.6 6.6l2.2-2.2c.3-.3.7-.4 1-.2 1.1.4 2.3.6 3.6.6.6 0 1 .4 1 1V20c0 .6-.4 1-1 1A17 17 0 0 1 3 4c0-.6.4-1 1-1h3.5c.6 0 1 .4 1 1 0 1.3.2 2.5.6 3.6.1.3 0 .7-.2 1z"/></svg>
        044-555 010 200
      </p>
      <p class="contact-line">
        <svg viewBox="0 0 24 24"><path d="M2 5h20v14H2z M2 5l10 8 10-8" /></svg>
        info@trenchline.com
      </p>
      <p class="address"><span class="address-label">Mailing Address</span><br>12345, Address Goes Here<br>Country Name, 123456.</p>
      <p class="address"><span class="address-label">Shop Address</span><br>12345, Address Goes Here<br>Country Name, 123456.</p>
    </div>

    <div class="brand">
      <div class="brand-mark"></div>
      <p class="brand-name"><span class="line-main">Trench Line</span><span class="line-sub">Contracting Inc</span></p>
    </div>
  </section>

</main>
</body>
</html>
```